TalkHarbor - Language Coaching Services

Sleek, innovative, trendy design for Language Coaching business.

TalkHarbor is a new UK based company that provides Language Coaching services. We offer highly personalized on-line and face to face language courses. We also impart learning techniques workshops based on the latest neuroscience research for second-language acquisition.

Target Market(s)

See attached info

Industry/Entity Type

Consulting

Contact Information for Business Card

TalkHarbor
DaniaKV@talkharbor.co.uk
TalkHarbor.co.uk
London, UK

Font styles to use
Sans Serif

```html
<!DOCTYPE html>
<html lang="en">
<head>
<meta charset="utf-8">
<title>TalkHarbor Business Card</title>
<link href="https://fonts.googleapis.com/css2?family=Montserrat:wght@500&family=Oswald:wght@400;600&family=Work+Sans:wght@400;500&display=swap" rel="stylesheet">
<style>
  :root {
    --page-bg: #151515;
    --card-bg: #232323;
    --card-edge: #2c2c2c;
    --accent: #12b4ec;
    --accent-deep: #0a86c2;
    --ink-light: #f2f2f2;
    --ink-muted: #d8d8d8;
  }
  * { margin: 0; padding: 0; box-sizing: border-box; }
  html, body { width: 1200px; height: 900px; overflow: hidden; }
  body {
    background: var(--page-bg);
    font-family: "Work Sans", sans-serif;
    position: relative;
  }
  .card {
    position: absolute;
    left: 290px;
    width: 620px;
    height: 354px;
    background: linear-gradient(135deg, var(--card-bg) 0%, var(--card-edge) 100%);
    border-bottom: 6px solid var(--accent);
    box-shadow: 0 18px 40px rgba(0,0,0,0.6);
  }
  .card--front { top: 70px; }
  .card--back { top: 476px; }

  /* Front */
  .brand {
    position: absolute;
    top: 58px;
    left: 0;
    width: 100%;
    display: flex;
    flex-direction: column;
    align-items: center;
  }
  .brand__circle {
    width: 118px;
    height: 118px;
    border: 7px solid var(--accent-deep);
    border-radius: 50%;
  }
  .brand__name {
    margin-top: 22px;
    font-family: "Montserrat", sans-serif;
    font-weight: 500;
    font-size: 50px;
    letter-spacing: 2px;
    color: var(--accent-deep);
    text-transform: uppercase;
  }
  .front__url {
    position: absolute;
    bottom: 26px;
    width: 100%;
    text-align: center;
    font-size: 15px;
    letter-spacing: 1px;
    color: var(--ink-light);
  }
  .front__url .hl, .contact .hl { color: var(--accent); }

  /* Back */
  .person {
    position: absolute;
    top: 122px;
    right: 348px;
    text-align: right;
  }
  .person__name {
    font-family: "Oswald", sans-serif;
    font-size: 40px;
    line-height: 1;
    letter-spacing: 1px;
    text-transform: uppercase;
  }
  .person__first { color: var(--accent-deep); font-weight: 400; }
  .person__last { color: var(--accent); font-weight: 600; }
  .person__role {
    margin-top: 8px;
    font-size: 17px;
    letter-spacing: 1px;
    color: var(--ink-light);
  }
  .divider {
    position: absolute;
    top: 120px;
    left: 298px;
    width: 2px;
    height: 70px;
    background: var(--ink-muted);
  }
  .contact {
    position: absolute;
    top: 122px;
    left: 322px;
    list-style: none;
  }
  .contact li {
    display: flex;
    align-items: center;
    gap: 10px;
    font-size: 16px;
    letter-spacing: 1px;
    color: var(--ink-light);
    line-height: 24px;
  }
  .contact svg { width: 12px; height: 12px; flex: none; }
  .address {
    position: absolute;
    bottom: 26px;
    width: 100%;
    text-align: center;
    font-size: 17px;
    letter-spacing: 1px;
    color: var(--ink-light);
  }
</style>
</head>
<body>
  <section class="card card--front">
    <div class="brand">
      <div class="brand__circle"></div>
      <div class="brand__name">TalkHarbor</div>
    </div>
    <p class="front__url">www.<span class="hl">talkharbor</span>.co.uk</p>
  </section>

  <section class="card card--back">
    <div class="person">
      <div class="person__name"><span class="person__first">Aaron</span> <span class="person__last">Whitlow</span></div>
      <div class="person__role">Director</div>
    </div>
    <div class="divider"></div>
    <ul class="contact">
      <li>
        <svg viewBox="0 0 12 12" aria-hidden="true"><path d="M3 1 L5 3.5 L4 4.8 Q5 7 7.2 8 L8.5 7 L11 9 L9.8 11 Q4 10.5 1 3 Z" fill="var(--accent)"/></svg>
        (555) 014-2207
      </li>
      <li>
        <svg viewBox="0 0 12 12" aria-hidden="true"><rect x="1" y="2.5" width="10" height="7" fill="none" stroke="var(--accent)" stroke-width="1.2"/><path d="M1 2.5 L6 6.5 L11 2.5" fill="none" stroke="var(--accent)" stroke-width="1.2"/></svg>
        info@talkharbor.co.uk
      </li>
      <li>
        <svg viewBox="0 0 12 12" aria-hidden="true"><circle cx="6" cy="6" r="5" fill="none" stroke="var(--accent)" stroke-width="1.1"/><ellipse cx="6" cy="6" rx="2.2" ry="5" fill="none" stroke="var(--accent)" stroke-width="1"/><path d="M1 6 H11" stroke="var(--accent)" stroke-width="1"/></svg>
        www.<span class="hl">talkharbor</span>.co.uk
      </li>
    </ul>
    <p class="address">41b Harbour Lane, London, UK, E14 2PL</p>
  </section>
</body>
</html>
```